Real-Estate business needs e-newsletter design for mail-chimp

We need a newsletter design as a PSD file.

Features of the e-newsletter design should include;

1. Our Corporate Colours and Logo - refer www.quorvatehomes.com.au
2. Our website menu items so readers can reference our services
3. Format should include our newsletter articles - usually 2 or 3 articles
4. Format should include a "special offer" section
5. Format should include our facebook likes widget as it appears on our website
6. Format should include company directors profile with "linked in" icon

```html
<!DOCTYPE html>
<html lang="en">
<head>
<meta charset="utf-8">
<title>Quorvate Homes Newsletter</title>
<link href="https://fonts.googleapis.com/css2?family=Questrial&family=Didact+Gothic&family=Poiret+One&display=swap" rel="stylesheet">
<style>
:root{
  --navy:#0d4a8b;
  --ink:#1b1b1b;
  --grey-text:#3a3a3a;
  --link:#2a5d9a;
  --dark:#2e2e2e;
  --white:#ffffff;
  --promo:#2d5a8e;
}
*{margin:0;padding:0;box-sizing:border-box}
html,body{width:921px;height:1200px;overflow:hidden;background:var(--white)}
body{position:relative;font-family:"Questrial",sans-serif;color:var(--ink)}
.site-header{position:absolute;left:0;top:0;width:921px;height:120px}
.brand{position:absolute;left:30px;top:42px;font-family:"Questrial",sans-serif;font-size:33px;letter-spacing:1px;color:var(--ink)}
.top-nav{position:absolute;right:35px;top:60px;display:flex;font-size:14px;letter-spacing:.5px}
.top-nav span{padding:0 21px}
.top-nav span+span{border-left:1.5px solid var(--ink)}
.top-nav span:last-child{padding-right:0}
.hero{position:absolute;left:0;top:120px;width:921px;height:295px;
  background:linear-gradient(180deg,#8d8d8f 0%,#b4b4b6 45%,#6a6a6c 72%,#2a2a2c 100%)}
.hero-title{position:absolute;top:88px;width:100%;text-align:center;color:var(--white);font-family:"Didact Gothic",sans-serif;font-size:26px}
.hero-rule{position:absolute;left:222px;top:140px;width:474px;height:2px;background:var(--white)}
.hero-sub{position:absolute;top:162px;width:100%;text-align:center;color:var(--white);font-family:"Didact Gothic",sans-serif;font-size:28px}
.service-nav{position:absolute;left:0;top:415px;width:921px;height:37px;background:var(--navy);color:var(--white);font-size:12.5px;letter-spacing:.4px}
.service-nav span{position:absolute;top:11px}
.article{position:absolute;top:513px;width:239px}
.article h2{height:39px;background:var(--navy);color:var(--white);font-family:"Didact Gothic",sans-serif;font-weight:400;font-size:16px;line-height:17px;text-align:center;display:flex;align-items:center;justify-content:center;padding:0 4px;letter-spacing:-.3px}
.article p{margin:16px 10px 0;height:104px;font-size:12px;line-height:18.4px;font-variant:small-caps;color:var(--grey-text);border-bottom:none}
.article .rule{height:2px;background:var(--navy);margin-top:0}
.article .more{text-align:right;padding-right:8px;margin-top:5px;color:var(--link);font-family:"Didact Gothic",sans-serif;font-size:16px}
.promo{position:absolute;left:66px;top:729px;width:789px;height:339px;background:radial-gradient(circle at 45% 60%,#5a83b4 0%,#375f90 45%,#223f66 100%)}
.promo-title{position:absolute;right:24px;top:83px;color:var(--white);font-family:"Poiret One",sans-serif;font-size:44px;line-height:46px;text-align:left}
.promo-bar{position:absolute;left:0;bottom:0;width:100%;height:46px;background:var(--dark);color:#cfcfcf;font-family:"Didact Gothic",sans-serif;font-size:22px;line-height:46px;padding-left:24px;word-spacing:3px}
.promo-bar b{font-weight:400;color:var(--white)}
.like-widget{position:absolute;left:70px;top:1083px;width:190px;height:74px}
.like-photo{position:absolute;left:6px;top:4px;width:40px;height:44px;background:linear-gradient(#cfd3d8,#8a8f96)}
.like-name{position:absolute;left:49px;top:6px;font-family:Arial,sans-serif;font-weight:bold;font-size:11.5px;color:#3b5998}
.like-btn{position:absolute;left:49px;top:23px;width:42px;height:16px;background:#4267b2;color:var(--white);font:bold 10px/16px Arial,sans-serif;text-align:center}
.like-divider{position:absolute;left:0;top:55px;width:190px;height:1px;background:#dde}
.like-count{position:absolute;left:1px;top:61px;font:10px Arial,sans-serif;color:#333}
.like-count span{color:#3b5998}
.site-footer{position:absolute;left:0;top:1166px;width:921px;height:34px;background:var(--dark);color:var(--white)}
.site-footer .url{position:absolute;left:0;width:100%;text-align:center;top:8px;font-size:15px}
.social{position:absolute;top:10px;width:16px;height:16px;background:#9a9a9a}
</style>
</head>
<body>
<header class="site-header">
  <div class="brand">QUORVATE HOMES</div>
  <nav class="top-nav"><span>ABOUT US</span><span>CONTACT US</span><span>LOGIN</span></nav>
</header>

<section class="hero" role="img" aria-label="Black and white city harbour skyline at dusk">
  <div class="hero-title">Let Us Help You......</div>
  <div class="hero-rule"></div>
  <div class="hero-sub">SAVE MONEY &amp; REDUCE RISK IN PROPERTY</div>
</section>

<nav class="service-nav">
  <span style="left:141px">BUYERS AGENT</span>
  <span style="left:274px">PROPERTY ADVICE</span>
  <span style="left:440px">PROPERTY MANAGEMENT</span>
  <span style="left:639px">ARTICLES &amp; RESOURCES</span>
</nav>

<article class="article" style="left:66px">
  <h2>The Property Investors Duty of Care</h2>
  <p>The recent deaths of five children in rental properties throughout the country has highlighted the need for a greater awareness of the maintenance required</p>
  <div class="rule"></div>
  <div class="more">Read more</div>
</article>
<article class="article" style="left:342px">
  <h2>Buying Well in a Hot Market</h2>
  <p>Investors shouldn't be lured in a false sense of security or a false economy in this market. The market will not keep going up indefinitely and interest rates</p>
  <div class="rule"></div>
  <div class="more">Read more</div>
</article>
<article class="article" style="left:616px">
  <h2>How did your Australian home get its look</h2>
  <p>Australian homes are made up of many different architectural styles? Have you ever wondered how the different styles came to be? What is your favorite?</p>
  <div class="rule"></div>
  <div class="more">Read more</div>
</article>

<section class="promo" role="img" aria-label="Blue toned photo of hands holding a small model house among model homes">
  <div class="promo-title">free property<br>management<br>for 2 months</div>
  <div class="promo-bar"><b>Call us today</b> to take advantage of our limited special offer on 1300 642 917.</div>
</section>

<aside class="like-widget">
  <div class="like-photo" role="img" aria-label="Director profile photo"></div>
  <div class="like-name">Quorvate Homes</div>
  <div class="like-btn">Like</div>
  <div class="like-divider"></div>
  <div class="like-count">508 people like <span>Quorvate Homes</span>.</div>
</aside>

<footer class="site-footer">
  <div class="url">www.quorvatehomes.com.au</div>
  <div class="social" style="left:753px"></div>
  <div class="social" style="left:788px"></div>
</footer>
</body>
</html>
```